Business Card Update, need to bring life to the card, two sided color

We need a new business card design, are moving and changing addresses and need a new look, we have the logos already attached but need a new style moving forward. Can incorporate the color of the logo (The Green) as well, maybe a solid back? We deal with safety products revolving around static electricity and safety lighting. Would like to keep same font in second logo as well.

Target Market(s)

Electrical Safety, Lighting

Contact Information for Business Card

Dale Fenwick
Vice President
Office: 770-555-4821
Cell: 770-555-3067
dale@tkfenwick.example
www.tkfenwick.example
4700 West Harbor Boulevard
Suite #150
Roswell, GA 30076

Font styles to use
Serif
Sans Serif

Requirements
Must have
• Since 1918
Nice to have
• Could use the 100 Year Logo for back of card, would like the back of card to be the same green as logo.
Should not have
• No black cards please.

```html
<!DOCTYPE html>
<html lang="en">
<head>
<meta charset="utf-8">
<title>T.K. Fenwick Business Card</title>
<link rel="stylesheet" href="https://fonts.googleapis.com/css2?family=Arimo:wght@700&family=Open+Sans:wght@400;600&display=swap">
<style>
  :root {
    --brand-green: #009a57;
    --card-grey: #dedede;
    --ink: #1c1c1c;
    --rule: #8a8a8a;
    --stage: #4a4a4a;
    --white: #ffffff;
  }
  * { box-sizing: border-box; margin: 0; padding: 0; }
  html, body { width: 1200px; height: 896px; overflow: hidden; }
  body {
    background: var(--stage);
    font-family: "Open Sans", Arial, sans-serif;
    display: flex;
    flex-direction: column;
    align-items: center;
    justify-content: center;
    gap: 32px;
  }
  .card {
    position: relative;
    width: 700px;
    height: 400px;
    overflow: hidden;
  }
  /* Front */
  .card-front { background: var(--card-grey); }
  .card-front::after {
    content: "";
    position: absolute;
    left: 0; right: 0; bottom: 0;
    height: 16px;
    background: var(--brand-green);
  }
  .faint-mark {
    position: absolute;
    left: 70px; top: -90px;
    width: 330px; height: 330px;
    border-radius: 50%;
    background: rgba(0,0,0,0.035);
  }
  .contact {
    position: absolute;
    left: 52px; top: 78px;
    width: 250px;
  }
  .person-name {
    font-weight: 600;
    font-size: 30px;
    color: var(--brand-green);
    line-height: 1.1;
  }
  .person-title {
    font-size: 17px;
    color: var(--ink);
    padding-bottom: 10px;
    border-bottom: 1px solid var(--rule);
    margin-bottom: 10px;
  }
  .contact-line {
    display: flex;
    align-items: center;
    gap: 8px;
    font-size: 17px;
    color: var(--ink);
    line-height: 1.45;
  }
  .contact-line svg { width: 14px; height: 14px; fill: var(--brand-green); flex: none; }
  .company {
    position: absolute;
    left: 330px; top: 96px;
    display: flex;
    align-items: center;
    gap: 16px;
  }
  .company-dot {
    width: 84px; height: 84px;
    border-radius: 50%;
    background: var(--brand-green);
    flex: none;
  }
  .company-name {
    font-family: "Arimo", Arial, sans-serif;
    font-weight: 700;
    color: var(--brand-green);
  }
  .company-name .main { display: block; font-size: 31px; line-height: 1.05; }
  .company-name .sub { display: block; font-size: 15px; }
  .address {
    position: absolute;
    right: 52px; bottom: 42px;
    width: 290px;
    border-top: 1px solid var(--rule);
    padding-top: 12px;
    text-align: right;
    font-size: 17px;
    color: var(--ink);
    line-height: 1.3;
  }
  /* Back */
  .card-back {
    background: var(--brand-green);
    display: flex;
    align-items: center;
    justify-content: center;
  }
  .card-back .faint-mark {
    left: 360px; top: 40px;
    width: 380px; height: 380px;
    background: rgba(255,255,255,0.06);
  }
  .back-name {
    position: relative;
    font-family: "Arimo", Arial, sans-serif;
    font-weight: 700;
    color: var(--white);
  }
  .back-name .main { display: block; font-size: 46px; line-height: 1.05; }
  .back-name .sub { display: block; font-size: 22px; }
  .back-name .since {
    display: block;
    margin-top: 10px;
    font-family: "Open Sans", Arial, sans-serif;
    font-weight: 600;
    font-size: 16px;
    letter-spacing: 3px;
    text-transform: uppercase;
  }
</style>
</head>
<body>
  <section class="card card-front" aria-label="Business card front">
    <div class="faint-mark" aria-hidden="true"></div>
    <div class="contact">
      <p class="person-name">Dale Fenwick</p>
      <p class="person-title">Vice President</p>
      <p class="contact-line">
        <svg viewBox="0 0 16 16" aria-hidden="true"><path d="M2 5c0-2 2-3 6-3s6 1 6 3v1h-3V5H5v1H2zM4 7h8l2 7H2z"/></svg>
        770-555-4821
      </p>
      <p class="contact-line">
        <svg viewBox="0 0 16 16" aria-hidden="true"><path d="M4 1h8v14H4zM5.5 2.5v9h5v-9z"/></svg>
        770-555-3067
      </p>
      <p class="contact-line">
        <svg viewBox="0 0 16 16" aria-hidden="true"><path d="M1 3h14v10H1zM2.5 4.5 8 9l5.5-4.5z"/></svg>
        dale@tkfenwick.example
      </p>
    </div>
    <div class="company">
      <span class="company-dot" aria-hidden="true"></span>
      <p class="company-name">
        <span class="main">T.K. Fenwick</span>
        <span class="sub">Manufacturing Company, Inc.</span>
      </p>
    </div>
    <p class="address">4700 West Harbor Boulevard<br>Suite #150<br>Roswell, GA 30076</p>
  </section>

  <section class="card card-back" aria-label="Business card back">
    <div class="faint-mark" aria-hidden="true"></div>
    <p class="back-name">
      <span class="main">T.K. Fenwick</span>
      <span class="sub">Manufacturing Company, Inc.</span>
      <span class="since">Since 1918</span>
    </p>
  </section>
</body>
</html>
```